Need CATCHY/VIVID Banner design for my new UTV/ATV/Off Road Vehicle turn signal/lighting company

I need a banner ad designed so I can advertise on several different ATV (all terrain vehicle), UTV (Utility Vehicles), Golf Cart and Off-Road Vehicle forums. Ads need to be very catchy and produce a call to action. Action is getting hits to my website. Our main business is selling turn signal kits to make your side by side or your ATV/UTV street legal, as some states now allow you to drive these on public roads if you have the following items: Turn Signals, Horn, Lighted license plate bracket, headlights and brake lights. We sell all of these items for just about any model vehicle out there. Our call to action for this banner would be to get more website visits.

Target Market(s)

Off-road/outdoor enthusiasts,

Industry/Entity Type

Car Accessorie

Font styles to use
Sans Serif

Requirements
Must have
• Ad size need to be either 728x90 or 300x250. Colorful ad with an off-road vehicle integrated to the design (think UTV, side-by-side, etc.
Nice to have
• Nice to haves would be anything that makes this banner ad stand out on very boring web pages.
Should not have
• anything dull

```html
<!DOCTYPE html>
<html lang="en">
<head>
<meta charset="utf-8">
<title>TrailBeam – ATV &amp; UTV Signal Kits Banner</title>
<link href="https://fonts.googleapis.com/css2?family=Roboto:wght@700;900&display=swap" rel="stylesheet">
<style>
  :root {
    --red-deep: #d3101c;
    --red: #e42a1a;
    --orange: #f06a17;
    --amber: #f7a51f;
    --white: #ffffff;
    --vehicle-dark: #2a2a2c;
    --vehicle-mid: #6f6a66;
  }
  html, body {
    margin: 0;
    padding: 0;
    overflow: hidden;
    background: var(--white);
  }
  .banner {
    position: relative;
    width: 1200px;
    height: 148px;
    overflow: hidden;
    background:
      radial-gradient(ellipse 420px 120px at 720px 150px, rgba(247,165,31,0.75), transparent 70%),
      linear-gradient(180deg, var(--red-deep) 0%, var(--red) 28%, var(--orange) 62%, var(--amber) 100%);
    font-family: "Roboto", Arial, sans-serif;
    color: var(--white);
  }
  .brand {
    position: absolute;
    left: 26px;
    top: 0;
    width: 250px;
    height: 148px;
    display: flex;
    align-items: center;
    justify-content: center;
    gap: 10px;
  }
  .brand-mark {
    width: 18px;
    height: 18px;
    background: var(--white);
  }
  .brand-name {
    font-weight: 900;
    font-size: 34px;
    letter-spacing: 1px;
    text-transform: uppercase;
  }
  .vehicle {
    position: absolute;
    border-radius: 10px;
  }
  .vehicle-sport {
    left: 322px;
    top: 22px;
    width: 188px;
    height: 120px;
    background: linear-gradient(160deg, #b9b3ad 0%, var(--vehicle-mid) 45%, var(--vehicle-dark) 100%);
  }
  .vehicle-utility {
    left: 958px;
    top: 4px;
    width: 196px;
    height: 140px;
    background: linear-gradient(170deg, #4a4a4c 0%, var(--vehicle-dark) 55%, #151516 100%);
  }
  .headline {
    position: absolute;
    left: 520px;
    width: 420px;
    top: 20px;
    text-align: center;
  }
  .headline-title {
    margin: 0;
    font-weight: 700;
    font-size: 37px;
    line-height: 1;
    letter-spacing: 0.5px;
    text-transform: uppercase;
  }
  .headline-sub {
    margin: 8px 0 0;
    font-weight: 700;
    font-size: 19px;
    line-height: 1;
    letter-spacing: 0.3px;
    text-transform: uppercase;
  }
  .feature-icons {
    position: absolute;
    left: 596px;
    top: 98px;
    display: flex;
    gap: 32px;
    align-items: center;
  }
  .feature-icons svg {
    display: block;
    height: 28px;
    fill: none;
    stroke: var(--white);
    stroke-width: 2.4;
    stroke-linecap: round;
    stroke-linejoin: round;
  }
  .feature-icons .solid { fill: var(--white); stroke: none; }
</style>
</head>
<body>
<div class="banner">
  <div class="brand">
    <span class="brand-mark"></span>
    <span class="brand-name">TrailBeam</span>
  </div>

  <div class="vehicle vehicle-sport" role="img" aria-label="Photo of a sport side-by-side off-road vehicle"></div>

  <div class="headline">
    <h1 class="headline-title">ATV &amp; UTV Vechicle</h1>
    <p class="headline-sub">Signal Kits and Lighting</p>
  </div>

  <div class="feature-icons">
    <svg viewBox="0 0 36 30" aria-label="Brake light">
      <circle cx="18" cy="15" r="10"/>
      <path d="M6 5 A14 14 0 0 0 6 25 M30 5 A14 14 0 0 1 30 25"/>
      <path d="M18 9 V16"/>
      <circle class="solid" cx="18" cy="20.5" r="1.6"/>
    </svg>
    <svg viewBox="0 0 36 30" aria-label="Headlight">
      <path class="solid" d="M16 5 C28 5 30 25 16 25 Z"/>
      <path d="M2 8 H11 M2 13 H11 M2 18 H11 M2 23 H11"/>
    </svg>
    <svg viewBox="0 0 48 30" aria-label="Horn">
      <path class="solid" d="M14 12 L34 4 V26 L14 18 Z"/>
      <rect class="solid" x="10" y="12" width="5" height="6"/>
      <path d="M8 8 L3 5 M8 15 H2 M8 22 L3 25"/>
    </svg>
    <svg viewBox="0 0 54 30" aria-label="Turn signals">
      <path d="M13 4 L2 15 L13 26 V20 H22 V10 H13 Z"/>
      <path d="M41 4 L52 15 L41 26 V20 H32 V10 H41 Z"/>
    </svg>
    <svg viewBox="0 0 24 30" aria-label="Signal light">
      <rect class="solid" x="6" y="1" width="12" height="28" rx="3"/>
      <path d="M2 6 H6 M18 6 H22 M2 15 H6 M18 15 H22 M2 24 H6 M18 24 H22"/>
      <circle cx="12" cy="6" r="2.6" fill="#e8431a" stroke="none"/>
      <circle cx="12" cy="15" r="2.6" fill="#e8431a" stroke="none"/>
      <circle cx="12" cy="24" r="2.6" fill="#e8431a" stroke="none"/>
    </svg>
  </div>

  <div class="vehicle vehicle-utility" role="img" aria-label="Photo of a utility side-by-side vehicle with cargo bed"></div>
</div>
</body>
</html>
```